Want a package created for a new protein bar

We would like a new package created for a new protein bar project The name of the bar will be VORNBar a real food protein bar, we would like a ‘window’ on the package of bar like Bold Meadow bar below in images.

VORNBar
‘Super Food Bar’
14g of Whey Protein
The package film size is the following 12cm width x 15cm Length,
Flavor Peanut Chocolate Chip, additional information will be attached shortly like nutrition facts,

Target Market(s)

fitness market, bodybuilders, athletes, everyday people

Industry/Entity Type

Health Product

Logo Text

VORNBar

Font styles to use
Serif
Sans Serif
Decorative

Requirements
Must have
• Package window

```html
<!DOCTYPE html>
<html lang="en">
<head>
<meta charset="utf-8">
<title>VORNBar Whey Protein Super Food Bar – Wrapper</title>
<link rel="stylesheet" href="https://fonts.googleapis.com/css2?family=Russo+One&family=Saira+Condensed:wght@600;700&display=swap">
<style>
  :root {
    --backdrop: #dde2fb;
    --wrapper-orange: #ea9b24;
    --crimp-orange: #f0a83a;
    --crimp-line: #f6c47a;
    --ink: #111111;
    --paper: #ffffff;
    --window-edge: #e9e9ee;
    --bar-brown: #8a6a5f;
    --bar-brown-dark: #6e5148;
  }
  html, body {
    margin: 0;
    padding: 0;
    overflow: hidden;
  }
  .canvas {
    position: relative;
    width: 1200px;
    height: 857px;
    background: var(--backdrop);
    overflow: hidden;
  }
  .wrapper-art {
    position: absolute;
    left: 0;
    top: 0;
  }
  .brand {
    position: absolute;
    left: 374px;
    top: 320px;
    display: flex;
    align-items: center;
    gap: 8px;
    font-family: "Russo One", sans-serif;
    font-size: 24px;
    color: var(--ink);
    letter-spacing: 1px;
  }
  .brand-square {
    width: 14px;
    height: 14px;
    background: var(--ink);
  }
  .headline {
    position: absolute;
    left: 268px;
    top: 364px;
    margin: 0;
    font-family: "Russo One", sans-serif;
    font-weight: 400;
    font-size: 44px;
    line-height: 1;
    color: var(--ink);
    font-style: italic;
    letter-spacing: 1px;
  }
  .subline {
    position: absolute;
    left: 268px;
    top: 414px;
    margin: 0;
    font-family: "Russo One", sans-serif;
    font-size: 27px;
    line-height: 1;
    color: var(--ink);
    font-style: italic;
    letter-spacing: 2px;
  }
  .flavor-band {
    position: absolute;
    left: 268px;
    top: 455px;
    width: 300px;
    height: 30px;
    background: var(--ink);
    color: var(--paper);
    font-family: "Saira Condensed", sans-serif;
    font-weight: 700;
    font-size: 18px;
    line-height: 30px;
    padding-left: 6px;
    box-sizing: border-box;
    letter-spacing: 0.2px;
  }
  .protein-amount {
    position: absolute;
    left: 628px;
    top: 494px;
    font-family: "Saira Condensed", sans-serif;
    font-weight: 700;
    font-size: 28px;
    line-height: 1;
    color: var(--ink);
  }
</style>
</head>
<body>
<main class="canvas">
  <svg class="wrapper-art" width="1200" height="857" viewBox="0 0 1200 857">
    <defs>
      <linearGradient id="barFill" x1="0" y1="0" x2="0" y2="1">
        <stop offset="0" stop-color="var(--bar-brown)"/>
        <stop offset="1" stop-color="var(--bar-brown-dark)"/>
      </linearGradient>
    </defs>
    <!-- wrapper body -->
    <rect class="wrapper-body" x="152" y="260" width="888" height="318" fill="var(--wrapper-orange)"/>
    <!-- left crimp seal -->
    <g class="crimp-left">
      <rect x="152" y="260" width="80" height="318" fill="var(--crimp-orange)"/>
      <rect x="166" y="262" width="4" height="314" fill="var(--crimp-line)"/>
      <rect x="180" y="262" width="4" height="314" fill="var(--crimp-line)"/>
      <rect x="194" y="262" width="4" height="314" fill="var(--crimp-line)"/>
      <rect x="208" y="262" width="4" height="314" fill="var(--crimp-line)"/>
    </g>
    <!-- window panel -->
    <polygon class="window-panel" points="732,292 940,292 912,578 700,578" fill="var(--paper)"/>
    <polygon class="divider-left" points="726,292 734,292 704,578 696,578" fill="var(--ink)"/>
    <polygon class="divider-right" points="940,262 947,262 911,578 904,578" fill="var(--ink)"/>
    <rect class="window-opening" x="725" y="337" width="172" height="146" rx="10" fill="url(#barFill)" stroke="var(--window-edge)" stroke-width="2" role="img" aria-label="Clear window showing the chocolate-coated protein bar inside"/>
    <!-- right crimp seal -->
    <g class="crimp-right">
      <rect x="955" y="260" width="85" height="318" fill="var(--crimp-orange)"/>
      <rect x="972" y="262" width="4" height="314" fill="var(--crimp-line)"/>
      <rect x="988" y="262" width="4" height="314" fill="var(--crimp-line)"/>
      <rect x="1004" y="262" width="4" height="314" fill="var(--crimp-line)"/>
      <rect x="1020" y="262" width="4" height="314" fill="var(--crimp-line)"/>
    </g>
  </svg>

  <div class="brand"><span class="brand-square"></span>VORNBAR</div>
  <h1 class="headline">WHEY PROTEIN</h1>
  <p class="subline">SUPER FOOD BAR</p>
  <div class="flavor-band">PEANUT CHOCOLATE CHIP FLAVOR</div>
  <div class="protein-amount">14G</div>
</main>
</body>
</html>
```